KRWB new business card design

We need a business card design for our established business which is Australia wide however based in Melbourne. We are a young team of Financial Planners who specialize in Insurance and Basic super advice for people like us.

We are people who help our clients get things done in a timely and cost effective manner whilst having a good time and a laugh along the way.

We would like this to have a consistent feel with our new e-brochure which i have attached from a color and font perspective.

Industry/Entity Type

Business

Requirements
Must have
• We do not need specific address details rather just the states we are in:

VIC/NSW/QLD/TAS
Nice to have
• Curved edge to mate the brochure

```html
<!DOCTYPE html>
<html lang="en">
<head>
<meta charset="utf-8">
<title>KRWB business card concepts</title>
<link href="https://fonts.googleapis.com/css2?family=Questrial&family=Didact+Gothic&display=swap" rel="stylesheet">
<style>
:root{
  --ink:#0b0b0b;
  --green:#8cc63f;
  --green-deep:#1fa54a;
  --panel:#6cc04a;
  --white:#ffffff;
  --bg:#e8e5e0;
  --radius:22px;
}
*{box-sizing:border-box;margin:0;padding:0}
html,body{width:1200px;height:502px;overflow:hidden}
body{background:var(--bg);font-family:"Questrial",sans-serif;color:var(--white);position:relative}
.card{position:absolute;background:var(--ink);overflow:hidden;border-radius:2px 2px var(--radius) 2px}
.brand{display:flex;align-items:center;gap:8px;font-family:"Questrial",sans-serif;color:var(--green);letter-spacing:2px}
.brand-square{background:var(--green-deep);flex:none}
.brand--white{color:var(--white)}
.brand--white .brand-square{background:var(--white)}
.heading{font-weight:700;letter-spacing:2.5px;font-family:"Didact Gothic",sans-serif}
.services{list-style:none}
.services li{white-space:nowrap}
.services li::before{content:"";display:inline-block;width:5px;height:5px;border-radius:50%;background:var(--green);margin-right:6px;vertical-align:middle}
.centered{position:absolute;left:0;right:0;text-align:center}

/* card 1 : contact */
.card--contact{left:36px;top:28px;width:354px;height:205px}
.card--contact .panel{position:absolute;left:150px;top:0;right:0;bottom:0;background:var(--panel);clip-path:polygon(22px 0,100% 0,100% 100%,0 100%)}
.card--contact .brand{position:absolute;left:30px;top:85px;font-size:30px}
.card--contact .brand-square{width:16px;height:16px}
.contact{position:absolute;left:172px;top:30px;font-size:8.5px;line-height:1.35;color:var(--white)}
.contact .name{font-size:12px;font-weight:700}
.contact .name em{font-weight:400}
.contact .role{font-size:10px;margin-bottom:10px}
.contact .row{display:flex;gap:10px;align-items:center;margin-bottom:3px}
.contact .row span{display:flex;align-items:center;gap:3px}
.contact svg{width:8px;height:8px;fill:var(--white)}
.contact .states{margin:9px 0 10px;letter-spacing:1px}
.contact .legal{font-size:8px;line-height:1.25}

/* card 2 : photo */
.card--photo{left:425px;top:28px;width:354px;height:202px}
.card--photo .stripe{position:absolute;right:52px;top:0;bottom:0;width:4px;background:var(--green)}
.card--photo .portrait{position:absolute;right:0;top:0;width:52px;height:100%;background:linear-gradient(180deg,#bdbdbd,#5a5a5a)}
.card--photo .brand{position:absolute;left:0;right:56px;justify-content:center;top:48px;font-size:28px}
.card--photo .brand-square{width:15px;height:15px}
.card--photo .heading{position:absolute;left:0;right:56px;text-align:center;top:128px;font-size:11px}
.card--photo .services{position:absolute;left:0;right:56px;top:146px;text-align:center;font-size:11.5px;line-height:18px}
.card--photo .services li{display:inline-block;margin:0 3px}

/* card 3 */
.card--columns{left:815px;top:31px;width:354px;height:205px}
.card--columns .brand{justify-content:center;top:50px;font-size:30px}
.card--columns .brand-square{width:16px;height:16px}
.card--columns .heading{top:140px;font-size:12px}
.card--columns .cols{position:absolute;left:12px;right:12px;top:166px;display:flex;justify-content:center;gap:6px;font-size:10.5px;line-height:15px}
.card--columns .col{padding-right:4px}
.card--columns .col + .col{border-left:1px solid var(--green-deep);padding-left:6px}
.card--columns .col:last-child{align-self:flex-end;padding-right:0}
.card--columns .services li::before{margin-right:5px}

/* card 4 */
.card--mono{left:36px;top:273px;width:354px;height:206px}
.card--mono .brand{justify-content:center;top:50px;font-size:30px}
.card--mono .brand-square{width:16px;height:16px}
.card--mono .heading{top:125px;font-size:12px}
.card--mono .services{top:144px;font-size:12px;line-height:18px}
.card--mono .services li{display:inline-block;margin:0 3px}
.card--mono .services li::before{background:var(--white)}
.card--mono .web{top:182px;font-size:11px;letter-spacing:3px}

/* card 5 */
.card--split{left:433px;top:273px;width:354px;height:202px;border-right:4px solid var(--green)}
.card--split .brand{position:absolute;left:34px;top:86px;font-size:28px}
.card--split .brand-square{width:15px;height:15px}
.card--split .divider{position:absolute;left:174px;top:42px;width:1px;height:72px;background:linear-gradient(180deg,transparent,#fff,transparent)}
.card--split .heading{position:absolute;left:190px;top:40px;font-size:12px}
.card--split .services{position:absolute;left:190px;top:64px;font-size:12px;line-height:21px}

/* card 6 */
.card--list{left:818px;top:278px;width:354px;height:205px}
.card--list .heading{position:absolute;left:26px;top:26px;font-size:14px}
.card--list .services{position:absolute;left:26px;top:54px;font-size:15px;line-height:25px}
.card--list .services li::before{width:6px;height:6px;margin-right:8px}
.card--list .brand{position:absolute;right:24px;top:90px;font-size:28px}
.card--list .brand-square{width:15px;height:15px}
</style>
</head>
<body>

<section class="card card--contact">
  <div class="panel"></div>
  <div class="brand"><span class="brand-square"></span>KRWB</div>
  <div class="contact">
    <p class="name">Jordan Ellery <em>ADFS, BBus, LRS©</em></p>
    <p class="role">Financial Adviser</p>
    <p class="row">
      <span><svg viewBox="0 0 10 10"><path d="M2 0h2l1 3-1.5 1a6 6 0 0 0 2.5 2.5L7 5l3 1v2c0 1-1 2-2 2A8 8 0 0 1 0 2c0-1 1-2 2-2z"/></svg>1300 555 214</span>
      <span><svg viewBox="0 0 10 10"><rect x="2.5" y="0" width="5" height="10" rx="1"/></svg>0400 555 718</span>
    </p>
    <p class="row">
      <span><svg viewBox="0 0 10 10"><rect x="0" y="4" width="10" height="6"/><rect x="2" y="0" width="6" height="4"/></svg>03 9000 0412</span>
      <span><svg viewBox="0 0 10 10"><path d="M0 2h10v6H0z"/></svg>jordan@krwb.com.au</span>
    </p>
    <p class="row">
      <span><svg viewBox="0 0 10 10"><circle cx="5" cy="5" r="5"/></svg>www.krwb.com.au</span>
    </p>
    <p class="states">VIC/NSW/QLD/TAS</p>
    <p class="legal">KRWB Planning Pty Ltd<br>Authorised Representatives<br>Harbourline Financial Planning Limited<br>Australian Financial Services Licensee</p>
  </div>
</section>

<section class="card card--photo">
  <div class="brand"><span class="brand-square"></span>KRWB</div>
  <p class="heading">Specialising in:</p>
  <ul class="services">
    <li>Risk Insurance</li><li>Debt Management</li><br>
    <li>Superannuation</li><br>
    <li>Wealth Creation</li><li>Retirement Planning</li>
  </ul>
  <div class="stripe"></div>
  <div class="portrait" role="img" aria-label="Portrait photo of a team member"></div>
</section>

<section class="card card--columns">
  <div class="brand centered"><span class="brand-square"></span>KRWB</div>
  <p class="heading centered">Specialising in:</p>
  <div class="cols">
    <ul class="services col"><li>Risk Insurance</li><li>Debt Management</li></ul>
    <ul class="services col"><li>Superannuation</li><li>Wealth Creation</li></ul>
    <ul class="services col"><li>Retirement Planning</li></ul>
  </div>
</section>

<section class="card card--mono">
  <div class="brand brand--white centered"><span class="brand-square"></span>KRWB</div>
  <p class="heading centered">Specialising in:</p>
  <ul class="services centered">
    <li>Risk Insurance</li><li>Debt Management</li><li>Superannuation</li><br>
    <li>Wealth Creation</li><li>Retirement Planning</li>
  </ul>
  <p class="web centered">www.krwb.com.au</p>
</section>

<section class="card card--split">
  <div class="brand"><span class="brand-square"></span>KRWB</div>
  <div class="divider"></div>
  <p class="heading">Specialising in:</p>
  <ul class="services">
    <li>Risk Insurance</li><li>Debt Management</li><li>Superannuation</li><li>Wealth Creation</li><li>Retirement Planning</li>
  </ul>
</section>

<section class="card card--list">
  <p class="heading">Specialising in:</p>
  <ul class="services">
    <li>Risk Insurance</li><li>Debt Management</li><li>Superannuation</li><li>Wealth Creation</li><li>Retirement Planning</li>
  </ul>
  <div class="brand"><span class="brand-square"></span>KRWB</div>
</section>

</body>
</html>
```